Re-design an HTML Website

Website must be responsive/fluid and designed with mobile-first priority. I want to be able to make changes with a HTML editor

We offer EMF Protection devices that neutralize EMF radiations emitted from electronics. We have devices for people and cell phones.
.

Redesign our Website (www.brightpebs.us) to look more modern, but I need to keep it in an HTML format. I plan on keeping the same shopping cart service (CraftLedger.com), as it has some features we need, but it is BUTTON intensive.

Requirements requested (samples submitted):
Headers and Footers
Menu setup as submitted
Creative Landing Page
Categories Page (must be stacked products)
Products Page (must be stacked products)
Individual Product Page
Generic 1-Column Page
Generic 2-Column Page
Generic 3-Column Page
Updates

What we sell are devices to neutralize the electromagnetic radiation (EMF) emitted from cell phones and electronics. Anything thing you can do to bring this website (www.BrightPEBs.us) into the 21st Century will be appreciated. It is a secondary website for our Affiliate Accounts - our primary site is at Vendaro www.PrimeEMFGoods.com

Be creative -- make us look and feel great!

Thanks, Oliver

Providing both a Mobile & Desktop screen shot would be helpful.

Also, do not use the products from pulsewafers.com - it is a slightly different product.
www.PrimeEMFGoods.com or www.BrightPEBs.us are our product configurations.

Industry/Entity Type

Technologoy

Coding

Coded - Design and coding required

Number of Pages Required

5+ page

Requirements
Must have
• Zip file and desciptions included
Nice to have
• Menu / footer /header / Landing page / Product Page / Category Page

```html
<!DOCTYPE html>
<html lang="en">
<head>
<meta charset="utf-8">
<title>Bright Pebs – EMF Protection Products</title>
<meta name="viewport" content="width=1200">
<link href="https://fonts.googleapis.com/css2?family=Inter:wght@400;500;600;700;800&display=swap" rel="stylesheet">
<style>
:root{
  --blue:#1e5590;
  --navy:#0c2a52;
  --yellow:#ffff00;
  --nav-bg:#4a4a48;
  --text:#1b1b1b;
  --muted:#666;
  --border:#d9d9d9;
  --white:#fff;
}
*{box-sizing:border-box;margin:0;padding:0}
html,body{width:1200px;height:3281px;overflow:hidden}
body{font-family:"Inter",Arial,sans-serif;color:var(--text);background:var(--white)}
a{color:inherit;text-decoration:none}

.topbar{height:43px;background:var(--blue);color:var(--white);font-size:14px;display:flex;align-items:center;justify-content:center}
.nav{height:81px;background:var(--nav-bg);display:flex;align-items:center;padding:0 110px;position:relative;z-index:2}
.brand{color:var(--white);font-weight:700;font-size:30px;margin-right:54px}
.menu{display:flex;align-items:center;gap:33px;color:var(--white);font-size:14px;font-weight:500;height:100%}
.menu .active{background:var(--yellow);color:var(--text);height:100%;display:flex;align-items:center;padding:0 14px;position:relative;margin-right:-13px}
.menu .active::after{content:"";position:absolute;left:0;right:0;bottom:-14px;height:14px;background:var(--yellow);clip-path:polygon(0 0,100% 0,50% 100%)}

.hero{height:565px;position:relative;background:linear-gradient(160deg,#6b6f6d 0%,#3c3e3c 45%,#1c1d1c 100%);overflow:hidden}
.hero .photo{position:absolute;inset:0;background:radial-gradient(ellipse at 55% 40%,#8a8c8a 0%,#4d4f4d 45%,#232423 100%)}
.hero h1{position:absolute;left:0;right:0;top:404px;text-align:center;color:var(--white);font-size:90px;font-weight:800;letter-spacing:1px}
.arrow{position:absolute;top:434px;width:46px;height:46px;border-radius:50%;background:rgba(255,255,255,.45);display:flex;align-items:center;justify-content:center}
.arrow.prev{left:64px}.arrow.next{right:64px}

.products{padding-top:85px;height:1083px}
.section-title{text-align:center;font-size:38px;font-weight:800;letter-spacing:.3px}
.tabs{display:flex;justify-content:center;gap:6px;margin-top:22px}
.tab{width:234px;height:41px;border-radius:21px;background:var(--blue);color:var(--white);font-weight:700;font-size:14px;display:flex;align-items:center;justify-content:center;position:relative}
.tab.on{background:var(--yellow);color:var(--text)}
.tab.on::after{content:"";position:absolute;bottom:-17px;left:50%;margin-left:-7px;border:7px solid transparent;border-top:8px solid var(--blue)}
.grid{display:grid;grid-template-columns:478px 478px;gap:24px 23px;margin:38px 0 0 111px}
.card{height:360px;border:1px solid var(--border);display:flex;padding:26px 0 0 38px}
.card .pic{width:110px;height:262px;background:linear-gradient(180deg,#f2f2f2,#d6d6d6 60%,#b9b0c4);border-radius:4px;flex:none}
.card .info{margin-left:53px;width:252px}
.kind{color:var(--blue);font-weight:700;font-size:14px;margin-top:6px}
.pkg{font-weight:600;font-size:15px;margin-top:11px}
.price{color:var(--blue);font-weight:700;font-size:24px;margin-top:5px}
.desc{color:var(--muted);font-size:14px;line-height:21.5px;margin-top:12px}
.desc+.desc{margin-top:21px}
.btn-outline{display:flex;align-items:center;justify-content:center;width:234px;height:41px;border:2px solid var(--blue);border-radius:21px;color:var(--blue);font-weight:700;font-size:14px;position:absolute;bottom:35px}
.card .info{position:relative;height:334px}

.consult{height:648px;background:var(--blue);position:relative;overflow:hidden;color:var(--white)}
.consult svg.bg{position:absolute;inset:0}
.consult .text{position:absolute;left:110px;top:78px;width:442px}
.consult h2{font-size:39px;font-weight:800;line-height:47px}
.consult .cred{font-size:14px;font-weight:700;margin-top:10px}
.consult p{font-size:14.5px;line-height:21.5px;margin-top:21px;text-align:justify}
.consult .cred+p{margin-top:30px}
.consult .sub{font-size:14px;font-weight:700;margin-top:21px}
.btn-yellow{display:flex;align-items:center;justify-content:center;width:234px;height:41px;border-radius:21px;background:var(--yellow);color:var(--text);font-weight:600;font-size:14px;margin-top:22px}
.portrait{position:absolute;left:698px;top:94px;width:296px;height:440px;background:linear-gradient(180deg,#8a6a52 0%,#b48e78 30%,#2d6b72 55%,#1f555c 100%);border-radius:140px 140px 0 0}
.name-bar{position:absolute;left:632px;top:534px;width:568px;height:114px;background:var(--navy);display:flex;align-items:center;padding-left:36px;font-size:21px;font-weight:700}

.commit{height:690px;text-align:center;padding-top:86px}
.commit h2{font-size:38px;font-weight:800}
.commit h3{color:var(--blue);font-size:26px;font-weight:700;margin-top:18px}
.commit p{width:890px;margin:23px auto 0;color:var(--muted);font-size:14px;line-height:21.5px}
.commit p+p{margin-top:21px}
.btn-blue{display:inline-flex;align-items:center;justify-content:center;width:234px;height:41px;border-radius:21px;background:var(--blue);color:var(--white);font-weight:700;font-size:12.5px;margin-top:23px}

.footer{height:323px;background:var(--navy);color:var(--white);text-align:center;position:relative;padding-top:50px}
.footer .disc{font-size:14px;line-height:21.5px;width:810px;margin:0 auto}
.footer hr{border:0;border-top:1px solid #9aa7b8;width:977px;margin:25px auto 0}
.footer .links{display:flex;justify-content:center;gap:82px;margin-top:36px;font-size:15px}
.footer .copy{margin-top:32px;font-size:15px}
.footer .code{position:absolute;right:45px;top:247px;font-size:12px}
</style>
</head>
<body>

<div class="topbar">Free Shipping Over $299</div>

<header class="nav">
  <a class="brand" href="#">Bright Pebs</a>
  <nav class="menu">
    <a class="active" href="#">Home</a>
    <a href="#">EMF Protection Devices</a>
    <a href="#">Savings Options</a>
    <a href="#">Why these Products / &nbsp;Recommendations</a>
    <a href="#">More &#8964;</a>
  </nav>
</header>

<section class="hero">
  <div class="photo" role="img" aria-label="Two smiling colleagues working at a laptop with colourful protection dots on its lid"></div>
  <h1>BRIGHT PEBS</h1>
  <a class="arrow prev" href="#" aria-label="Previous slide"><svg width="12" height="12" viewBox="0 0 12 12"><path d="M8 1 3 6l5 5" fill="none" stroke="#fff" stroke-width="1.6"/></svg></a>
  <a class="arrow next" href="#" aria-label="Next slide"><svg width="12" height="12" viewBox="0 0 12 12"><path d="M4 1l5 5-5 5" fill="none" stroke="#fff" stroke-width="1.6"/></svg></a>
</section>

<section class="products">
  <h2 class="section-title">EMF PROTECTION PRODUCTS</h2>
  <div class="tabs">
    <a class="tab" href="#">FOR ALL ELECTRONICS</a>
    <a class="tab on" href="#">FOR YOU</a>
    <a class="tab" href="#">FOR THE HOME</a>
  </div>
  <div class="grid">
    <article class="card">
      <div class="pic" role="img" aria-label="TAG starter package: white and black pendants on cords plus phone with dots"></div>
      <div class="info">
        <div class="kind">TAG</div>
        <div class="pkg">STARTER PACKAGE</div>
        <div class="price">$69.95</div>
        <p class="desc">Includes the Body/Bio PEB embedded in the TAG for you to wear or keep near you to strengthen and balance your energy field.</p>
        <p class="desc">Plus 1 Bright PEB Set– &nbsp;For your cell phone Personal wearable technology!</p>
        <a class="btn-outline" href="#">VIEW DETAILS</a>
      </div>
    </article>
    <article class="card">
      <div class="pic" role="img" aria-label="CLIP starter package: white and black pendants plus phone with dots"></div>
      <div class="info">
        <div class="kind">CLIP</div>
        <div class="pkg">STARTER PACKAGE</div>
        <div class="price">$69.95</div>
        <p class="desc">Includes the Body/Bio PEB embedded in the CLIP for you to wear or keep near you to strengthen and balance your energy field.</p>
        <p class="desc">Plus 1 Bright PEB Set – For your cell phone</p>
        <a class="btn-outline" href="#">VIEW DETAILS</a>
      </div>
    </article>
    <article class="card">
      <div class="pic" role="img" aria-label="BAND starter package: white and black wristbands plus phone with dots"></div>
      <div class="info">
        <div class="kind">WRISTBAND</div>
        <div class="pkg">STARTER PACKAGE</div>
        <div class="price">$69.95</div>
        <p class="desc">Includes the Body/Bio PEB embedded in the wristBAND for you to wear or keep near you to strengthen and balance your energy field.</p>
        <p class="desc">Plus 1 Bright PEB Set – For your cell phone</p>
        <a class="btn-outline" href="#">VIEW DETAILS</a>
      </div>
    </article>
    <article class="card">
      <div class="pic" role="img" aria-label="TRIPLE starter package: three colourful adhesive dots plus phone with dots"></div>
      <div class="info">
        <div class="kind">BODY/BIO PEB</div>
        <div class="pkg">STARTER PACKAGE</div>
        <div class="price">$69.95</div>
        <p class="desc">Includes the Body/Bio PEB &nbsp;adhesive PEB, which can be adhered to a watch or favorite piece of jewelry (or carry in a pocket). Optional use: place on cell with Bright PEB to receive the wearable benefits.</p>
        <a class="btn-outline" href="#">VIEW DETAILS</a>
      </div>
    </article>
  </div>
</section>

<section class="consult">
  <svg class="bg" width="1200" height="648" viewBox="0 0 1200 648" aria-hidden="true">
    <polygon points="955,0 1200,0 1200,534 688,534" fill="#ffff00"/>
  </svg>
  <div class="text">
    <h2>EDUCATIONAL HEALTH CONSULTATION</h2>
    <div class="cred">WITH MARGARET HOLLOWAY, CLS, NCMP, PH.D.</div>
    <p>Clinical Laboratory Scientist – Global Menopause Assn. Certified Menopause Practitioner – Medical Researcher – Author</p>
    <p>Also specializing in electromagnetic fields (EMF) symptoms resolution. Understanding what you are going through and how to get help can be a difficult and tedious process.</p>
    <p>Dr. Holloway's 25 years of experience allows her to quickly assess what works and what does not. Her goal is to get you on the right track so that you can obtain the health care that is best for you and your family.</p>
    <div class="sub">ELECTROMAGNETIC SENSITIVITY CONSULTATIONS</div>
    <a class="btn-yellow" href="#">CONSULTATION</a>
  </div>
  <div class="portrait" role="img" aria-label="Portrait of the consultant in a teal jacket"></div>
  <div class="name-bar">MARGARET HOLLOWAY, CLS, NCMP, PH.D.</div>
</section>

<section class="commit">
  <h2>OUR COMMITMENT</h2>
  <h3>"OFFER THE BEST AVAILABLE EMF PRODUCTS!"</h3>
  <p>As researchers, we will continue to search for the most effective EMF products and make them available to you and your families. &nbsp;We encourage families to cover the environments and devices they can control-and you will do better than your neighbors. &nbsp;Most are choosing to ignore or discount the scientific evidence proving the harm EMF creates.</p>
  <p>Please contact us with any questions, as this product line is a little complicated &nbsp;and well worth the time investment to ensure you obtain the best coverage possible. &nbsp;We utilize customized Bright PEB Sets to offset the extreme EMF exposures we are subjected to here in the USA-EMF exposures are not going to go away, and we all need to cover as many electronic devices as possible.</p>
  <a class="btn-blue" href="#">oliver@brightPEBs.us</a>
</section>

<footer class="footer">
  <div class="disc">Disclaimers:<br>Statements on this website have not been evaluated by the Food and Drug Administration.<br>These products are not intended to diagnose, treat, cure or prevent any disease. Consumers are advised to do their own research.</div>
  <hr>
  <div class="links"><a href="#">PRIVACY POLICY</a><a href="#">RETURNS POLICY</a><a href="#">CONTACT</a></div>
  <div class="copy">© 2024 Copyrights | All Rights Reserved</div>
  <div class="code">C38</div>
</footer>

</body>
</html>
```